Refresh of far from plain IT company website

Our web site is starting to show it's age. You can see the existing site here: www.plumbwick.net. As a growing company we want to come across as a dynamic collection of IT experts.

We want to update the design so are open to any colour palette and look, but want to retain our current table logo. We use the logo on our business cards but with a white background - see the attached file, so you don't need to keep the brown or the green.

The design should consider the range of browsers that will be looking at the site - so please show how it will look on a wide screen laptop and a 768x1024 tablet.

We want to add some pages about our team and their skills, probably with photos of each person on the team.

This is an uncoded project - the PSD files of the design is required, not coding.
Updates

Thanks everyone for the submissions so far.  It's a holiday day in the UK today but we will get some feedback on the designs so far out to you.

Target Market(s)

Architects and other creative types looking for IT support

Industry/Entity Type

Business

Font styles to use
Serif
Sans Serif

Requirements
Must have
• Must look good on a laptop and an iPad.

```html
<!DOCTYPE html>
<html lang="en">
<head>
<meta charset="utf-8">
<title>plumbwick – IT services</title>
<link href="https://fonts.googleapis.com/css2?family=Open+Sans:wght@400;600;700&family=Source+Sans+3:wght@400;600;700&display=swap" rel="stylesheet">
<style>
:root{
  --plum:#8c0b4b;
  --plum-light:#a8125f;
  --plum-dark:#6e0639;
  --gold:#dcad05;
  --ink:#3d3d3d;
  --muted:#8a8a8a;
  --grey-icon:#b9b9b9;
  --page-bg:#f2f2f2;
  --line:#e2e2e2;
}
*{box-sizing:border-box;margin:0;padding:0}
html,body{width:873px;height:1200px;overflow:hidden}
body{background:var(--page-bg);font-family:"Source Sans 3",sans-serif;color:var(--ink);position:relative}
.top-rule{position:absolute;left:0;top:0;width:873px;height:2px;background:var(--plum)}
.sheet{position:absolute;left:62px;top:0;width:748px;height:1131px;background:#fff;box-shadow:0 0 4px rgba(0,0,0,.08)}
.abs{position:absolute}

/* header */
.brand{left:73px;top:26px;display:flex;align-items:center;gap:9px}
.brand-mark{width:22px;height:22px;background:var(--gold)}
.brand-name{font-family:"Open Sans",sans-serif;font-weight:700;font-size:28px;color:var(--plum);letter-spacing:-.3px}
.phone{left:582px;top:22px;display:flex;align-items:center;gap:10px;font-family:"Open Sans",sans-serif;font-size:11px;color:#888}
.phone .sep{width:1px;height:26px;background:var(--line)}
.auth{top:22px;height:16px;font-family:"Open Sans",sans-serif;font-size:7.5px;font-weight:600;color:#fff;display:flex;align-items:center;justify-content:center}
.auth.login{left:724px;width:36px;background:var(--plum)}
.auth.signup{left:764px;width:36px;background:#7a7a7a}
.search{left:645px;top:48px;width:155px;height:17px;background:#eeeeee}
.search-btn{left:779px;top:48px;width:21px;height:17px;background:var(--gold);display:flex;align-items:center;justify-content:center}

/* nav */
.main-nav{left:73px;top:86px;width:727px;height:35px;background:linear-gradient(var(--plum-light),var(--plum-dark));display:flex}
.main-nav a{color:#fff;text-decoration:none;font-family:"Open Sans",sans-serif;font-size:10.5px;display:flex;align-items:center;justify-content:center;border-right:1px solid rgba(0,0,0,.12)}
.main-nav a.active{background:rgba(0,0,0,.22)}

/* hero */
.hero{left:73px;top:121px;width:727px;height:325px;background:radial-gradient(circle at 54% 55%,#c22a2a 0,#5a1a1a 14%,#2c3440 32%,#121418 70%,#050505 100%)}
.hero-arrow{width:16px;height:16px;border-radius:50%;display:flex;align-items:center;justify-content:center}
.hero-arrow.prev{left:100px;top:269px;background:rgba(140,11,75,.5)}
.hero-arrow.next{left:754px;top:269px;background:rgba(255,255,255,.25)}
.hero-title{left:132px;top:291px;width:273px;height:32px;background:var(--gold);color:#fff;font-family:"Open Sans",sans-serif;font-weight:600;font-size:19px;padding-left:18px;line-height:32px}
.hero-text{left:134px;top:334px;width:333px;height:53px;background:rgba(40,40,40,.75);color:#fff;font-family:"Open Sans",sans-serif;font-size:10px;line-height:19px;padding:6px 0 0 17px}
.dots{left:411px;top:459px;display:flex;gap:5px}
.dots span{width:6px;height:6px;border-radius:50%;background:#c9c9c9}
.dots span.on{background:var(--plum)}

/* services */
.section-title{left:0;width:873px;text-align:center;font-family:"Open Sans",sans-serif}
.services-title{top:493px;font-size:23px;color:#444}
.services-sub{top:524px;font-size:11px;color:var(--muted)}
.service{top:563px;width:190px;text-align:center}
.service .icon{width:52px;height:52px;border-radius:50%;background:var(--grey-icon);margin:0 auto;display:flex;align-items:center;justify-content:center}
.service h3{font-family:"Open Sans",sans-serif;font-weight:400;font-size:14px;color:#555;margin-top:15px}
.service p{font-family:"Open Sans",sans-serif;font-size:8.6px;color:#8a8a8a;line-height:11.3px;margin-top:10px}
.service.featured .icon{background:var(--plum)}
.service.featured h3{color:var(--plum)}
.read-more-btn{display:inline-block;margin-top:10px;background:var(--plum);color:#fff;font-family:"Open Sans",sans-serif;font-size:8.5px;font-weight:600;padding:3px 9px;border-radius:7px}

/* about / events */
.block-title{font-family:"Source Sans 3",sans-serif;font-weight:600;font-size:14px;color:var(--plum)}
.about-photo{left:73px;top:783px;width:87px;height:78px;background:linear-gradient(#3a7bc8,#a9c9ea 60%,#d8a98a)}
.about-text{font-size:9.4px;line-height:13.6px;color:#555;text-align:justify}
.events-more{left:750px;top:749px;font-family:"Open Sans",sans-serif;font-size:9px;color:#666}
.event-photo{width:88px;height:58px}
.event h4{font-family:"Open Sans",sans-serif;font-weight:400;font-size:12px;color:#333}
.event p{font-size:8.4px;line-height:11px;color:#777;text-align:justify;margin-top:6px}
.event time{display:block;text-align:right;font-size:8px;color:var(--plum);margin-top:4px}

/* clients */
.clients-title{top:976px;font-family:"Source Sans 3",sans-serif;font-weight:600;font-size:15px;color:var(--plum)}
.client{top:1014px;width:102px;height:61px;border:1px solid #e4e4e4;display:flex;align-items:center;justify-content:center;gap:5px;font-family:"Source Sans 3",sans-serif;font-weight:700;font-size:11px}
.client .dot{width:10px;height:10px;border-radius:50%}

/* footer */
.site-footer{left:0;top:1131px;width:873px;height:69px;background:var(--plum)}
.footer-links{left:63px;top:1151px;display:flex;gap:10px;font-size:10.5px;color:#fff;font-weight:600}
.copyright{left:63px;top:1171px;font-size:10px;color:#fff;font-weight:600}
.social{top:1155px;width:22px;height:22px;border-radius:50%;background:#fff}
</style>
</head>
<body>
<div class="top-rule"></div>
<div class="sheet"></div>

<header>
  <div class="abs brand"><span class="brand-mark"></span><span class="brand-name">plumbwick</span></div>
  <div class="abs phone">
    <svg width="14" height="16" viewBox="0 0 14 16"><path d="M3 1 L6 4 L4.5 6 C5.5 8.5 7 10 9.5 11.5 L11.5 10 L14 13 L11.5 15.5 C6 14 1.5 9.5 0.5 3.5 Z" fill="var(--plum)"/></svg>
    <span class="sep"></span>
    <span>+(49) 555 010 240</span>
  </div>
  <div class="abs auth login">Login</div>
  <div class="abs auth signup">SignUp</div>
  <div class="abs search"></div>
  <div class="abs search-btn"><svg width="8" height="8" viewBox="0 0 8 8"><circle cx="3.2" cy="3.2" r="2.3" fill="none" stroke="#fff" stroke-width="1.2"/><line x1="5" y1="5" x2="7.5" y2="7.5" stroke="#fff" stroke-width="1.3"/></svg></div>
</header>

<nav class="abs main-nav">
  <a class="active" style="width:100px">Home</a>
  <a style="width:107px">About us</a>
  <a style="width:94px">What we do</a>
  <a style="width:96px">News &amp; blog</a>
  <a style="width:96px">Articles</a>
  <a style="width:119px">Clients</a>
  <a style="width:115px;border-right:0">Partners</a>
</nav>

<section>
  <div class="abs hero" role="img" aria-label="Photo of a hand touching a glowing red gear among dark machine cogs"></div>
  <div class="abs hero-arrow prev"><svg width="6" height="8" viewBox="0 0 6 8"><path d="M5 0.5 L1.5 4 L5 7.5" fill="none" stroke="#fff" stroke-width="1.5"/></svg></div>
  <div class="abs hero-arrow next"><svg width="6" height="8" viewBox="0 0 6 8"><path d="M1 0.5 L4.5 4 L1 7.5" fill="none" stroke="#fff" stroke-width="1.5"/></svg></div>
  <div class="abs hero-title">Lorem ipsum dolor sit amit</div>
  <div class="abs hero-text">Dummy text of the printing and typesetting industry.<br>Lorem Ipsum has been the industry's standard dummy text</div>
  <div class="abs dots"><span class="on"></span><span></span><span></span></div>
</section>

<section>
  <h2 class="abs section-title services-title" style="font-weight:400">Our Service</h2>
  <p class="abs section-title services-sub">Lorem ipsum dolor sit amit contantry</p>

  <div class="abs service featured" style="left:57px">
    <div class="icon"><svg width="30" height="20" viewBox="0 0 30 20"><path d="M8 18 H23 A5.5 5.5 0 0 0 23 7 A8 8 0 0 0 8 8 A5 5 0 0 0 8 18 Z" fill="none" stroke="#fff" stroke-width="1.8"/></svg></div>
    <h3>Cloud Computing</h3>
    <p>Increase performane &amp; Avalibility<br>Geographic Sepration for failover<br>transfer of risk &amp; TCO</p>
    <span class="read-more-btn">Read More</span>
  </div>
  <div class="abs service" style="left:249px">
    <div class="icon"><svg width="24" height="22" viewBox="0 0 24 22"><ellipse cx="10" cy="4" rx="8" ry="3" fill="#fff"/><path d="M2 7 C2 10 18 10 18 7 V10 C18 13 2 13 2 10 Z M2 13 C2 16 12 16 14 15 V17 C10 19 2 18 2 16 Z" fill="#fff"/><circle cx="18" cy="16" r="4.5" fill="none" stroke="#fff" stroke-width="1.6"/></svg></div>
    <h3>Disaster Recovery</h3>
    <p>Difined RPO and RTO Objectives<br>Enter price Class Recoverablity<br>Low Incremental Costs</p>
  </div>
  <div class="abs service" style="left:440px">
    <div class="icon"><svg width="24" height="20" viewBox="0 0 24 20"><path d="M4 13 V10 A8 8 0 0 1 20 10 V13" fill="none" stroke="#fff" stroke-width="1.8"/><rect x="3" y="11" width="4" height="7" rx="1" fill="#fff"/><rect x="17" y="11" width="4" height="7" rx="1" fill="#fff"/></svg></div>
    <h3>IT Support &amp; Management</h3>
    <p>Client / server networks<br>Data and voice covergence<br>multisite Connectivity</p>
  </div>
  <div class="abs service" style="left:625px">
    <div class="icon"><svg width="22" height="22" viewBox="0 0 22 22"><rect x="2" y="2" width="12" height="12" rx="2" fill="none" stroke="#fff" stroke-width="2"/><rect x="8" y="8" width="12" height="12" rx="2" fill="none" stroke="#fff" stroke-width="2"/></svg></div>
    <h3>Virtualliztion</h3>
    <p>Server &amp; Storage Virtualization<br>Application Streamnig<br>Secure Remote Desktops</p>
  </div>
</section>

<section>
  <h2 class="abs block-title" style="left:73px;top:740px">About Us</h2>
  <div class="abs about-photo" role="img" aria-label="Photo of raised hands holding a globe under a blue sky"></div>
  <p class="abs about-text" style="left:178px;top:779px;width:352px">Plumbwick was established with a specific aim: to consistently deliver an advanced and comprehensive IT service for ambitious growing companies across all industry sectors. consectetur, from a Lorem Ipsum passage, and going through the cites of the word in classical literature, discovered the undoubtable source. Lorem Ipsum comes from sections .Ipsum is not simply random text. Igoing through the cites of the word in classical literature, discovered the undoubtable source.</p>
  <p class="abs about-text" style="left:73px;top:868px;width:457px">AnnouncementsContrary to popular belief, Lorem Ipsum is not simply random text. It has roots in a piece of classical Latin literature from 45 BC, making it over 2000 years old. Edwin Marlow, a Latin professor at Ashgrove College in Vermont, looked up one of the more obscure Latin words, consectetur, from a Lorem Ipsum passage, and</p>

  <h2 class="abs block-title" style="left:560px;top:742px">Events &amp; News</h2>
  <span class="abs events-more">Read More</span>

  <div class="abs event-photo" style="left:561px;top:782px;background:linear-gradient(135deg,#e8eef5,#5b8fd0 50%,#2a3a55)" role="img" aria-label="Illustration of a tablet surrounded by colourful app icons"></div>
  <div class="abs event" style="left:666px;top:781px;width:134px">
    <h4>Lorem ipsum dolor</h4>
    <p>Plumbwick launch smartphone and tablet apps</p>
    <time>Oct 30, 2014, 8:28 am</time>
  </div>

  <div class="abs event-photo" style="left:561px;top:858px;background:radial-gradient(circle at 60% 45%,#fff6c8,#e59a2a 30%,#2f6fb8 65%,#222 100%)" role="img" aria-label="Illustration of colourful app tiles bursting from a light source"></div>
  <div class="abs event" style="left:666px;top:855px;width:134px">
    <h4>Lorem ipsum dolor</h4>
    <p>Latin literature from 45 BC, making it over 2000 years old. Edwin Marlow,</p>
    <time>Oct 30, 2014, 8:28 am</time>
  </div>
</section>

<section>
  <h2 class="abs section-title clients-title">Some of our Clients who love being with us!</h2>
  <div class="abs client" style="left:73px;color:#e8632a"><span class="dot" style="background:#e8632a"></span>Hexaform</div>
  <div class="abs client" style="left:198px;color:#1f93c9">Northbay</div>
  <div class="abs client" style="left:323px;color:#8a7a5a">Foxley</div>
  <div class="abs client" style="left:448px;color:#7cae2a"><span class="dot" style="background:#7cae2a"></span>Brightbulb</div>
  <div class="abs client" style="left:573px;color:#e88a10">Orbit Design</div>
  <div class="abs client" style="left:698px;color:#2a7cc8">Signalpoint</div>
</section>

<footer>
  <div class="abs site-footer"></div>
  <div class="abs footer-links"><span>Contact Us</span><span>Privacy &amp; Security</span><span>Terms of Use</span><span>Opt-out</span></div>
  <div class="abs copyright">Copyright 2014 Plumbwick.net All Rights Rights Reserved</div>
  <span class="abs social" style="left:665px"></span>
  <span class="abs social" style="left:695px"></span>
  <span class="abs social" style="left:726px"></span>
  <span class="abs social" style="left:757px"></span>
  <span class="abs social" style="left:788px"></span>
</footer>
</body>
</html>
```